Tidy paddock Services

After a high quality design website. we are a company that provides services to people that own land and need a hand getting on top of the delayed jobs.
would want a number of tab/ pages for the web page.
Home page / About us page / services page / Gallery page. / Contact us page
we offer a wide range of services .listed below

Stock Work (title)

Stock movement
Break feeding
Temporary staffing

Spraying (title)

Spraying weeds
Spraying gorse

Pastures (title)

Fertilizing
Topping

Building (title)

Habitable sheds
Farm sheds
Sheep yards
Cattle yards
Repair farm buildings
Decks
Retaining walls

Fencing (title)

Stock fencing
Post & rail
Stock yards repair
Electric fencing install & repairs

Water Management (title)

Water trough installation
Water scheme install
Water trough cleaning
Farm water maintenance
Water ponds
Ornamental ponds
Drainage

General (title)

Lawn mowing
Hedge trimming
Pruning trees
Metaling drive ways & races
Water blasting
Small digger work
Little tip truck cartage
Home kill management
Mulching gorse
Section clearing

```html
<!DOCTYPE html>
<html lang="en">
<head>
<meta charset="utf-8">
<title>Tidy paddock Services</title>
<link href="https://fonts.googleapis.com/css2?family=Lato:wght@400;700;900&family=Roboto:wght@400;500;700&display=swap" rel="stylesheet">
<style>
:root{
  --green:#5f9b14;
  --green-dark:#4b8410;
  --green-light:#7bb52a;
  --black:#000;
  --ink:#1b1b1b;
  --muted:#6b6b6b;
  --panel:#f2f2f2;
  --white:#fff;
}
*{margin:0;padding:0;box-sizing:border-box}
html,body{width:1200px;height:4027px;overflow:hidden}
body{position:relative;background:var(--white);font-family:"Roboto",Arial,sans-serif;color:var(--ink)}
.abs{position:absolute}
.btn{position:absolute;display:flex;align-items:center;justify-content:center;gap:8px;border-radius:24px;background:var(--green);color:var(--white);font:700 14px "Roboto",Arial,sans-serif;text-transform:uppercase}
.btn .dot{width:13px;height:13px;border-radius:50%;background:var(--white);position:relative}
.btn .dot::after{content:"";position:absolute;left:4px;top:3.5px;border-left:5px solid var(--green);border-top:3px solid transparent;border-bottom:3px solid transparent}
.btn.dark{background:var(--black)}
.btn.dark .dot::after{border-left-color:var(--black)}

/* header */
.brand{left:144px;top:36px;display:flex;align-items:center;gap:12px}
.brand .mark{width:46px;height:46px;border-radius:50%;background:var(--green)}
.brand .name{font:700 26px "Lato",sans-serif;color:var(--green)}
.social-top{top:25px;width:38px;height:38px;border-radius:50%}
.call-label{left:753px;top:24px;font-size:13px}
.call-num{left:753px;top:44px;font-size:15px;font-weight:700}
.nav{left:437px;top:81px;width:763px;height:39px;background:var(--black);clip-path:polygon(22px 0,100% 0,100% 100%,0 100%)}
.nav a{position:absolute;top:12px;color:var(--white);font:500 14px "Roboto",sans-serif;text-decoration:none}

/* hero */
.hero-photo{left:0;top:120px;width:1200px;height:622px;background:linear-gradient(180deg,#bcd3e9 0%,#d8e3d4 45%,#b6c98a 70%,#7f9a45 100%)}
.hero-kicker{left:144px;top:252px;font:700 12px "Roboto",sans-serif;color:var(--green)}
.hero-title{left:144px;top:282px;font:900 46px "Lato",sans-serif;color:#111}
.hero-text{left:144px;top:346px;width:540px;font:500 16px/24px "Roboto",sans-serif;color:#111}

/* about */
.about-ring{left:150px;top:794px;width:384px;height:384px;border-radius:50%;border:8px solid var(--green);border-top-color:transparent;border-right-color:transparent;transform:rotate(10deg)}
.about-photo{left:155px;top:794px;width:380px;height:380px;border-radius:50%;background:linear-gradient(180deg,#8fb4d8,#c7b598 55%,#6e5a3e)}
.section-title{font:900 35px "Lato",sans-serif;color:var(--ink);display:flex;align-items:center;gap:16px}
.section-title .accent{color:var(--green)}
.section-title .rule{width:60px;height:3px;background:currentColor}
.about-body{left:620px;top:874px;width:435px;font:400 13px/24px "Roboto",sans-serif;color:var(--muted);text-align:justify}
.about-body p+p{margin-top:10px}

/* services */
.services-bg{left:0;top:1259px;width:1200px;height:944px;background:var(--panel)}
.tab{position:absolute;height:48px;border-radius:24px;background:var(--white);box-shadow:0 2px 6px rgba(0,0,0,.12);display:flex;align-items:center;font:500 15px "Roboto",sans-serif;color:#333}
.tab .num{width:48px;height:48px;border-radius:50%;background:var(--green);color:var(--white);font:500 24px "Roboto",sans-serif;display:flex;align-items:center;justify-content:center;margin-right:22px}
.tab .arr{margin-left:12px;width:22px;height:2px;background:currentColor;position:relative}
.tab .arr::after{content:"";position:absolute;right:0;top:-4px;width:8px;height:8px;border-top:2px solid currentColor;border-right:2px solid currentColor;transform:rotate(45deg)}
.tab.active{background:var(--green);color:var(--white)}
.tab.active .num{background:var(--black)}
.card{position:absolute;width:288px;height:242px;background:var(--white);box-shadow:0 2px 8px rgba(0,0,0,.12)}
.card .pic{height:184px}
.card .ico{position:absolute;left:114px;top:152px;width:60px;height:60px;border-radius:50%;background:var(--white);display:flex;align-items:center;justify-content:center}
.card .label{position:absolute;left:0;right:0;top:208px;text-align:center;font:500 16px "Roboto",sans-serif}
.card.featured{background:var(--green);color:var(--white);text-align:center}
.card.featured h3{margin-top:82px;font:500 16px "Roboto",sans-serif}
.card.featured p{margin:10px 20px 0;font:400 13px/22px "Roboto",sans-serif}
.dots{left:580px;top:2120px;display:flex;gap:6px}
.dots i{width:10px;height:10px;border-radius:50%;background:#999}
.dots i.on{background:var(--green)}

/* contact */
.contact-bg{left:0;top:2203px;width:1200px;height:542px;background:linear-gradient(135deg,#6fa81b,#548f0f 50%,#6aa318)}
.info{position:absolute;top:2340px;color:var(--white)}
.info b{display:block;font:700 15px "Roboto",sans-serif}
.info span{font:400 13px "Roboto",sans-serif}
.field{position:absolute;background:var(--white);border-radius:3px;font:400 13px "Roboto",sans-serif;color:#777;padding:14px 18px}

/* gallery */
.shot{position:absolute}

/* footer */
.foot-head{position:absolute;top:3776px;font:500 17px "Roboto",sans-serif;color:var(--white)}
.foot-list{position:absolute;top:3820px;list-style:none;font:400 12px/24px "Roboto",sans-serif;color:var(--white)}
.foot-list.icons li{display:flex;align-items:center;gap:8px;line-height:26px}
.foot-list .ic{width:8px;height:8px;background:var(--green);border-radius:50%}
.foot-social{position:absolute;top:3976px;width:28px;height:28px;border:2px solid var(--white);border-radius:50%}
.copyright{left:0;width:1200px;top:3984px;text-align:center;font:400 13px "Roboto",sans-serif;color:var(--white)}
</style>
</head>
<body>

<!-- HEADER -->
<div class="abs brand"><div class="mark"></div><div class="name">TIDY PADDOCK SERVICES</div></div>
<div class="abs social-top" style="left:575px;background:var(--green)" aria-label="Social link"></div>
<div class="abs social-top" style="left:619px;border:2px solid #ccc" aria-label="Social link"></div>
<svg class="abs" style="left:705px;top:24px" width="38" height="38" viewBox="0 0 38 38"><circle cx="19" cy="19" r="17" fill="none" stroke="var(--green)" stroke-width="2"/><path d="M12 11c2-2 4 0 5 2s-1 3-1 3 1 3 4 5c0 0 1-2 3-1s4 3 2 5c-3 3-9 0-12-4s-4-8-1-10z" fill="var(--green)"/></svg>
<div class="abs call-label">Call Us:</div>
<div class="abs call-num">+1-555-010-2040</div>
<div class="btn" style="left:903px;top:25px;width:152px;height:38px;font-size:14px">Get a Quoate</div>
<nav class="abs nav">
  <a style="left:54px">HOME</a><a style="left:155px">ABOUT US</a><a style="left:285px">SERVICES</a><a style="left:410px">GALLERY</a><a style="left:532px">CONTACT US</a>
</nav>

<!-- HERO -->
<div class="abs hero-photo" role="img" aria-label="Smiling farmer in cap and checked shirt using a tablet among young crop plants at sunrise"></div>
<svg class="abs" style="left:0;top:590px" width="1200" height="160" viewBox="0 0 1200 160">
  <path d="M0 30 C200 110 500 170 760 120 C900 95 1020 55 1200 40 L1200 160 L0 160Z" fill="var(--white)"/>
  <path d="M0 30 C200 110 500 170 760 120 C900 95 1020 55 1080 50 C1000 80 880 130 760 140 C500 175 200 140 0 70Z" fill="var(--green)"/>
  <circle cx="1070" cy="65" r="11" fill="var(--green)"/>
</svg>
<div class="abs hero-kicker">WELCOME TO</div>
<div class="abs hero-title">TIDY PADDOCK SERVICES</div>
<div class="abs hero-text">Lorem ipsum dolor sit amet, consectetur adipiscing elit, sed do eiusmod tempor incididunt ut labore et dolore magna aliqua.</div>
<div class="btn" style="left:144px;top:419px;width:189px;height:42px">Get Started <span class="dot"></span></div>

<!-- ABOUT -->
<div class="abs about-ring"></div>
<div class="abs about-photo" role="img" aria-label="Two farmers talking in a ploughed field at sunset"></div>
<div class="abs section-title" style="left:619px;top:812px"><span>ABOUT <span class="accent">US</span></span><span class="rule"></span></div>
<div class="abs about-body">
  <p>Lorem ipsum dolor sit amet, consectetur adipiscing elit, sed do eiusmod tempor incididunt ut labore et dolore magna aliqua. Ut enim ad minim veniam, quis nostrud exercitation ullamco laboris nisi ut aliquip ex ea commodo irure dolor in reprehenderit consequat.</p>
  <p>Sed ut perspiciatis unde omnis iste natus error sit voluptatem accusantium doloremque laudantium, totam rem aperiam, eaque ipsa quae ab illo inventore veritatis et quasi architecto beatae vitae dicta sunt ipsum voluptatem quia voluptas explicabo.</p>
</div>
<div class="btn" style="left:620px;top:1106px;width:143px;height:36px;font-size:13px">Learn More <span class="dot"></span></div>

<!-- SERVICES -->
<div class="abs services-bg"></div>
<div class="abs section-title" style="left:413px;top:1323px"><span class="rule"></span><span><span class="accent">OUR</span> SERVICES</span><span class="rule"></span></div>

<div class="tab" style="left:125px;top:1407px;width:219px"><span class="num">01</span>Stock Work<span class="arr"></span></div>
<div class="tab" style="left:370px;top:1407px;width:272px"><span class="num">02</span>Water Management<span class="arr"></span></div>
<div class="tab active" style="left:669px;top:1407px;width:192px"><span class="num">03</span>Building<span class="arr"></span></div>
<div class="tab" style="left:888px;top:1407px;width:185px"><span class="num">04</span>Spraying<span class="arr"></span></div>
<div class="tab" style="left:267px;top:1488px;width:202px"><span class="num">05</span>Pastures<span class="arr"></span></div>
<div class="tab" style="left:498px;top:1488px;width:202px"><span class="num">06</span>Fencing<span class="arr"></span></div>
<div class="tab" style="left:730px;top:1488px;width:203px"><span class="num">07</span>General<span class="arr"></span></div>

<div class="card" style="left:144px;top:1581px"><div class="pic" role="img" aria-label="Small timber shed with red roof on a lawn" style="background:linear-gradient(180deg,#6f9a4a,#b9b3a0 60%,#7aa04a)"></div><div class="ico"><svg width="30" height="26" viewBox="0 0 30 26"><path d="M2 11 15 2l13 9M5 10v14h20V10M10 24v-9h10v9" fill="none" stroke="#333" stroke-width="1.6"/></svg></div><div class="label">Habitable Sheds</div></div>
<div class="card featured" style="left:455px;top:1581px">
  <svg style="position:absolute;left:122px;top:26px" width="44" height="44" viewBox="0 0 44 44"><path d="M4 18 22 5l18 13M8 16v24h28V16M16 40V26h12v14M16 31h12M16 35h12" fill="none" stroke="#fff" stroke-width="2"/></svg>
  <h3>Farm Sheds</h3>
  <p>Lorem ipsum dolor sit amet, consectetur adipiscing elit, sed do eiusmod tempor incididunt ut labore et dolore magna aliqua.</p>
</div>
<div class="card" style="left:764px;top:1581px"><div class="pic" role="img" aria-label="Flock of sheep in a grassy field" style="background:linear-gradient(180deg,#c9b58e,#d9d3c4 50%,#7f9550)"></div><div class="ico"><svg width="28" height="28" viewBox="0 0 28 28"><circle cx="14" cy="14" r="10" fill="none" stroke="#333" stroke-width="1.6"/></svg></div><div class="label">Sheep Yards</div></div>

<div class="card" style="left:144px;top:1848px"><div class="pic" role="img" aria-label="Cattle grazing in a green pasture" style="background:linear-gradient(180deg,#a9c07c,#8a6a45 55%,#6f9a3a)"></div><div class="ico"><svg width="28" height="28" viewBox="0 0 28 28"><circle cx="14" cy="14" r="10" fill="none" stroke="#333" stroke-width="1.6"/></svg></div><div class="label">Cattle Yards</div></div>
<div class="card" style="left:455px;top:1848px"><div class="pic" role="img" aria-label="Brick farm building under scaffolding" style="background:linear-gradient(180deg,#c8ccd2,#9c6e55 60%,#8d8a84)"></div><div class="ico"><svg width="30" height="30" viewBox="0 0 30 30"><circle cx="15" cy="15" r="8" fill="none" stroke="#333" stroke-width="1.6"/><circle cx="15" cy="15" r="3" fill="none" stroke="#333" stroke-width="1.6"/></svg></div><div class="label">Repair Farm Buildings</div></div>
<div class="card" style="left:764px;top:1848px"><div class="pic" role="img" aria-label="Concrete block retaining wall under construction" style="background:linear-gradient(180deg,#6f8a55,#8b7358 55%,#d9cdb8)"></div><div class="ico"><svg width="30" height="26" viewBox="0 0 30 26"><path d="M3 22h24M3 17h24M8 17v5M16 17v5M22 17v5M18 14 26 3" fill="none" stroke="#333" stroke-width="1.6"/></svg></div><div class="label">Retaining Walls</div></div>

<div class="abs dots"><i></i><i class="on"></i><i></i></div>

<!-- CONTACT -->
<div class="abs contact-bg"></div>
<div class="abs section-title" style="left:422px;top:2261px;color:var(--white)"><span class="rule"></span><span>CONTACT US</span><span class="rule"></span></div>
<svg class="abs" style="left:208px;top:2336px" width="40" height="42" viewBox="0 0 40 42"><path d="M20 4a10 10 0 0 1 10 10c0 8-10 18-10 18S10 22 10 14A10 10 0 0 1 20 4z" fill="none" stroke="#111" stroke-width="2"/><circle cx="20" cy="14" r="4" fill="none" stroke="#111" stroke-width="2"/><path d="M4 38h32l-5-8M4 38l5-8" fill="none" stroke="#111" stroke-width="2"/></svg>
<div class="info" style="left:262px"><b>ADDRESS</b><span>14 Ridgeline Road, Fernvale 4821</span></div>
<svg class="abs" style="left:526px;top:2338px" width="40" height="40" viewBox="0 0 40 40"><path d="M8 6c3-3 6 0 8 3s-1 5-1 5 2 5 7 9c0 0 2-3 5-1s6 5 3 8c-5 5-14 0-19-6S4 10 8 6z" fill="none" stroke="#111" stroke-width="2"/></svg>
<div class="info" style="left:578px;top:2346px"><b>PHONE NUMBER</b><span>+1-555-010-2040</span></div>
<svg class="abs" style="left:756px;top:2344px" width="42" height="30" viewBox="0 0 42 30"><rect x="2" y="2" width="38" height="26" fill="none" stroke="#111" stroke-width="2"/><path d="M2 2l19 15L40 2M2 28l14-13M40 28 26 15" fill="none" stroke="#111" stroke-width="2"/></svg>
<div class="info" style="left:811px;top:2346px"><b>EMAIL</b><span>info@tidypaddockservices.com</span></div>

<div class="field" style="left:186px;top:2417px;width:402px;height:46px">Name</div>
<div class="field" style="left:186px;top:2478px;width:402px;height:46px">Email Address</div>
<div class="field" style="left:186px;top:2539px;width:402px;height:46px">Phone Number</div>
<div class="field" style="left:611px;top:2416px;width:405px;height:172px">Message</div>
<div class="btn dark" style="left:525px;top:2625px;width:150px;height:36px;font-size:13px">Submit Now <span class="dot"></span></div>

<!-- GALLERY -->
<div class="abs section-title" style="left:421px;top:2832px"><span class="rule"></span><span><span class="accent">OUR</span> GALLERY</span><span class="rule"></span></div>
<div class="shot" style="left:144px;top:2917px;width:450px;height:261px;background:linear-gradient(120deg,#2f4a2a,#5e7a45 50%,#c9a9a8)" role="img" aria-label="Worker in safety glasses spraying garden plants"></div>
<div class="shot" style="left:603px;top:2917px;width:452px;height:261px;background:linear-gradient(180deg,#a9b4bf,#6f6a63 55%,#8c8580)" role="img" aria-label="Engineer in hard hat reviewing plans on a construction site"></div>
<div class="shot" style="left:144px;top:3189px;width:300px;height:234px;background:linear-gradient(135deg,#8a4a2c,#a3a09a 55%,#7d7a73)" role="img" aria-label="Builder laying concrete blocks for a wall"></div>
<div class="shot" style="left:453px;top:3189px;width:289px;height:234px;background:linear-gradient(180deg,#6a5f55,#3f6a2c 50%,#6a9a3a)" role="img" aria-label="Gardener trimming hedges beside a fence"></div>
<div class="shot" style="left:752px;top:3189px;width:298px;height:234px;background:linear-gradient(135deg,#b8a68a,#4a5560 50%,#e5e5e5)" role="img" aria-label="Farmer with tablet beside dairy cows in a barn"></div>
<div class="btn" style="left:525px;top:3472px;width:150px;height:36px;font-size:13px">View More <span class="dot"></span></div>

<!-- FOOTER -->
<svg class="abs" style="left:0;top:3570px" width="1200" height="457" viewBox="0 0 1200 457">
  <path d="M0 140 C300 40 600 0 800 10 C950 18 1080 60 1200 100 L1200 457 L0 457Z" fill="var(--black)"/>
  <path d="M0 140 C300 40 600 0 800 10 C950 18 1080 60 1200 100 L1200 125 C1080 90 950 45 800 38 C600 30 300 75 0 165Z" fill="var(--green)"/>
  <circle cx="128" cy="62" r="9" fill="var(--green)"/>
  <line x1="0" y1="382" x2="1200" y2="382" stroke="#333" stroke-width="1"/>
</svg>
<div class="abs" style="left:0;width:1200px;top:3680px;display:flex;justify-content:center;align-items:center;gap:12px">
  <div style="width:40px;height:40px;border-radius:50%;background:var(--green)"></div>
  <div style="font:700 24px 'Lato',sans-serif;color:var(--green)">TIDY PADDOCK SERVICES</div>
</div>

<div class="foot-head" style="left:147px">QUICK LINKS</div>
<ul class="foot-list" style="left:146px"><li>Home</li><li>About Us</li><li>Services</li><li>Gallery</li><li>Contact Us</li></ul>
<div class="foot-head" style="left:559px">SERVICES</div>
<ul class="foot-list" style="left:559px"><li>Our Company</li><li>Privacy Policy</li><li>Latest News</li><li>Site Map</li></ul>
<div class="foot-head" style="left:858px">CONTACT US</div>
<ul class="foot-list icons" style="left:858px"><li><span class="ic"></span>14 Ridgeline Road, Fernvale 4821</li><li><span class="ic"></span>+1 555 010 2040</li><li><span class="ic"></span>info@tidypaddockservices.com</li></ul>

<div class="foot-social" style="left:146px" aria-label="Social link"></div>
<div class="foot-social" style="left:179px" aria-label="Social link"></div>
<div class="foot-social" style="left:212px" aria-label="Social link"></div>
<div class="foot-social" style="left:245px" aria-label="Social link"></div>
<div class="abs copyright">© Copyright 2024 &nbsp;/ Tidy paddock Services / All Rights Reserved</div>

</body>
</html>
```